Business Card Design

New business card design

Target Market(s)

Residential & Commercial Property Managers

Industry/Entity Type

Plumbing Services

Contact Information for Business Card

Name - Rowan Keddle, title - Director, Phone Number - 0431 286 517, email - rowan@tbk-plumbing.com.au, Company ABN - 73 215 904 386,

Font styles to use
Sans Serif

Colors
0054AA
0677BA
7BADD7
CADEEF
E8F1F8

```html
<!DOCTYPE html>
<html lang="en">
<head>
<meta charset="utf-8">
<title>TBK Plumbing Services – Business Card</title>
<link rel="stylesheet" href="https://fonts.googleapis.com/css2?family=Montserrat:wght@400;500;700&display=swap">
<style>
  :root {
    --backdrop: #232323;
    --card-white: #ffffff;
    --ink-dark: #1d2228;
    --brand-blue: #2ea8e0;
    --text-light: #ffffff;
    --tagline-grey: #5a4f4a;
  }
  * { box-sizing: border-box; margin: 0; padding: 0; }
  html, body {
    width: 1200px; height: 780px; overflow: hidden;
    background: var(--backdrop);
    font-family: "Montserrat", sans-serif;
  }
  .card {
    position: absolute;
    width: 560px; height: 320px;
    top: 230px;
    background: var(--card-white);
    border-radius: 26px;
    overflow: hidden;
    box-shadow: 0 4px 0 var(--brand-blue), 0 16px 30px rgba(0,0,0,.55);
  }
  .card--back { left: 25px; }
  .card--front { left: 615px; }

  .brand-name {
    position: absolute;
    color: var(--ink-dark);
    font-weight: 700;
    white-space: nowrap;
    display: flex; align-items: center; gap: 12px;
  }
  .brand-name__dot {
    width: 16px; height: 16px; border-radius: 50%;
    background: var(--brand-blue); flex: none;
  }
  .card--back .brand-name {
    left: 0; right: 0; top: 132px; justify-content: center;
    font-size: 38px; letter-spacing: 1px;
  }
  .card--front .brand-name {
    right: 30px; top: 40px; font-size: 24px; letter-spacing: .5px;
  }
  .card--front .brand-name__dot { width: 12px; height: 12px; }

  .wave { position: absolute; inset: 0; width: 100%; height: 100%; }

  .holder {
    position: absolute; left: 0; top: 104px;
    padding-left: 34px;
  }
  .holder__bar {
    position: absolute; left: 0; top: 6px;
    width: 24px; height: 50px; background: var(--brand-blue);
  }
  .holder__name {
    color: var(--brand-blue); font-weight: 700; font-size: 25px; line-height: 1.1;
  }
  .holder__title {
    color: var(--ink-dark); font-weight: 400; font-size: 16px; margin-top: 2px;
  }

  .contact {
    position: absolute; left: 110px; top: 222px;
    color: var(--text-light); font-size: 15px; line-height: 1.3;
  }
  .contact__abn { margin-bottom: 12px; }
  .contact__row { display: flex; align-items: center; gap: 8px; }
  .contact__icon { width: 15px; height: 15px; flex: none; }
</style>
</head>
<body>

<section class="card card--back" aria-label="Card back">
  <div class="brand-name"><span class="brand-name__dot"></span>TBK Plumbing Services</div>
</section>

<section class="card card--front" aria-label="Card front">
  <svg class="wave" viewBox="0 0 560 320" preserveAspectRatio="none" aria-hidden="true">
    <path d="M320,168 C420,172 500,150 545,95 L560,85 L560,102 C515,150 440,178 330,172 Z" fill="var(--brand-blue)"/>
    <path d="M260,170 C400,186 500,170 560,110 L560,122 C500,180 400,192 260,176 Z" fill="var(--brand-blue)"/>
    <path d="M0,205 C120,160 250,160 380,178 C470,190 520,170 560,128 L560,320 L0,320 Z" fill="var(--ink-dark)"/>
    <path d="M30,222 C140,182 260,176 380,184" fill="none" stroke="var(--card-white)" stroke-width="3"/>
  </svg>

  <div class="brand-name"><span class="brand-name__dot"></span>TBK Plumbing Services</div>

  <div class="holder">
    <span class="holder__bar"></span>
    <p class="holder__name">Rowan Keddle</p>
    <p class="holder__title">Director</p>
  </div>

  <div class="contact">
    <p class="contact__abn">Company ABN<br>- 73 215 904 386</p>
    <p class="contact__row">
      <svg class="contact__icon" viewBox="0 0 24 24" aria-hidden="true"><path fill="var(--brand-blue)" d="M6.6 10.8a15.1 15.1 0 0 0 6.6 6.6l2.2-2.2a1 1 0 0 1 1-.25 11.4 11.4 0 0 0 3.6.57 1 1 0 0 1 1 1V20a1 1 0 0 1-1 1A17 17 0 0 1 3 4a1 1 0 0 1 1-1h3.5a1 1 0 0 1 1 1c0 1.25.2 2.45.57 3.57a1 1 0 0 1-.25 1z"/></svg>
      0431 286 517
    </p>
    <p class="contact__row">
      <svg class="contact__icon" viewBox="0 0 24 24" aria-hidden="true"><path fill="var(--brand-blue)" d="M2 5h20v14H2z"/><path fill="none" stroke="var(--ink-dark)" stroke-width="2" d="M2 6l10 7 10-7"/></svg>
      rowan@tbk-plumbing.com.au
    </p>
  </div>
</section>

</body>
</html>
```